Store Front Window Design

We have a beautiful corner store front dental practice with no window signage. Crazy I know...that's why we need your help.

The final design will be done in all vinyl unless unless you suggest a different medium (meaning we are open to some design idea like using frosted glass, etc...).

The windows provide a lot of natural light so the design needs to keep a lot of natural light coming into the office. Keep in mind vinyl is not opaque so keep the signage aesthetically pleasing and a minimalist design to allow as much natural light in as possible. The design should follow the aesthetic from our logo. or tie into at least. We want a cohesive brand aesthetic.

I submitted some general layout ideas. There is a blue banner with advertising words which we want to be used in the final version. Even though the lettering is black, in reality the letters will be a white vinyl on the outside of the window. When you submit your work, be sure to add any special instructions (aka tell me the vision for the letters is white not black, maybe gold leaf, or forested glass...stuff like that). AND YOU DO NOT HAVE TO FOLLOW MY PATTERN! YOU ARE ARTISTS AND WE ARE LOOKING FOR AN ARTISTIC EYE CATCHING PRESENTATION OF THIS INFORMATION. MAKE IT FLASHY AND ADD SOME AESTHETIC FROM THE TOOTH LOGO.

The store front is 6 windows roughly 60'' x 36'' The smaller windows below are 27'' x 36''. Around the corner there are 3 windows. they are 60'' x 27'' lower windows are 27" x 27". We would like to keep the bottom windows clear and keep the signage on the top windows, however, we are flexible.

The front 6 windows need to have this information worked into the design.

Practice name: Varden and Pellosi Dental & Orthodontics.
Phone numbers: Rosalind Varden DDS: 415.555.0187
Oskar Pellosi DDS:415.555.0243

Expertise: Dr. Varden General Dentistry & Orthodontics
Dr. Pellosi Oral Surgery & Sedation

Address: 1938 Birchwood Ave

A banner across the bottom of the top windows with some key advertisement words: "Clearmold" "Braces" "Implants" "Whiting" "Call today" "Free Consultation" "Oral Surgery" "Sedation". We like the two color idea. Its up to you to decide on the color combo. I used a Dark and light blue, but maybe a Blue and grey would nice to tire in the logo colors?

I have made some mock ideas to get the ball rolling but you do not have to stick to these designs at all, just as long as all the required information is there. Be creative with the layouts, fonts, color scheme, (just remember these are going on windows not necessarily a white background), and graphics/artistic flare (refer to logo for layout inspiration and use the logo as an actual graphic). We are running a miltimillion dollar dental practice so we want these windows to be eye catching to pull in patients and look like a million dollar design. Also all 6 windows dont need ot be used. I am really looking for creative design marketing.

The corner 3 windows need the following information: name, expertise, phone number, banner.

Dr. Varden, General Dentistry & Orthodontics, 415.555.0187
Dr. Pellosi, Oral Surgery & Sedation, 415.555.0243

There is also a front door that needs to be designed. The door is 60'' x 36'' (standard door size) We want simple white vinyl on the outside of the door. We need you to organize the information on the door, pick a easy to read font, maybe use the logo and use some of the front window signage aesthetic? Its up to you...but we we were initially thinking of just making the litters white and keep it simple but again you are the designers.

Practice name: Varden and Pellosi General Dentistry & Orthodontics

Address: 1938 Birchwood Ave

Phone numbers: Dr. Varden 415.555.0187
Dr. Pellosi 415.555.0243

Hours of operation: Mon: call for an appointment
Tues-Thurs: 9am-5pm
Sat: call for an appointment
Sun: Closed

A line saying we speak Spanish: Se Habla Espanol

*****************************************************************************************************
here are some design that we liked and some rough sketches I made to start the ball rolling. Keep in mind that there are 9 windows for the front because its a corner office, but not all of them have to have stuff on it. We want simple, streamline, classy high commanding price point aesthetic. I am hiring you for your artistic minds.

Target Market(s)

anyone who has dental needs

Industry/Entity Type

Dental

Font styles to use
Serif
Sans Serif

Colors

Designer to choose colors to be used in the design.

Requirements
Must have
• 1. The required information (see project description)
• 2. Logo
• 3. Advertisement banner running along the bottom of all 9 windows (6 in front and 3 on the side)
• NOTE: Look at pictures of the store to get a sense of the customers point of view and also as a reference to how your design will be broken up across several windows or maybe you design something special for every window. But we want the banner to run along all the windows to lead customs to the door on the side. Finally the letters will be done in white vinyl unless state otherwise, remember the window needs to let in natural light so the entire window can not be covered in vinyl.
Nice to have
• artistic flare yet simple and sleep and expensive looking aesthetic. work logo into the design.
Should not have
• The goal is to catch someone eye and give them important information about the practice.
• It should not just be words.
• It should not have to many words
• It must be readable font for cards driving by.

```html
<!DOCTYPE html>
<html lang="en">
<head>
<meta charset="utf-8">
<title>Rosalind Varden D.D.S. — Window Panel</title>
<link href="https://fonts.googleapis.com/css2?family=Montserrat:wght@500;700&family=Oswald:wght@600&display=swap" rel="stylesheet">
<style>
  :root {
    --backdrop: #f2f2f2;
    --panel: #ffffff;
    --ink-dark: #1b6275;
    --ink-light: #4a98a5;
    --band: #4a97a3;
    --band-dark: #1b6275;
    --illus-a: #bfe6f6;
    --illus-b: #eaf6fb;
  }
  * { margin: 0; padding: 0; box-sizing: border-box; }
  html, body {
    width: 1200px; height: 1200px; overflow: hidden;
    background: var(--backdrop);
  }
  .panel {
    position: absolute; left: 237px; top: 0;
    width: 722px; height: 1200px;
    background: var(--panel);
    font-family: "Montserrat", sans-serif;
  }
  .illustration {
    position: absolute; left: 199px; top: 56px;
    width: 320px; height: 216px;
    border-radius: 24px;
    background: radial-gradient(ellipse at 60% 45%, var(--illus-a), var(--illus-b) 70%, var(--panel));
  }
  .doctor-name {
    position: absolute; left: 0; top: 308px; width: 100%;
    text-align: center; color: var(--ink-dark);
    font-weight: 700; font-size: 58px; line-height: 72px;
    letter-spacing: 0.01em;
  }
  .rule {
    position: absolute; left: 81px; width: 557px; height: 6px;
    border-top: 2px solid var(--ink-light);
    border-bottom: 2px solid var(--ink-light);
  }
  .rule-top { top: 486px; }
  .rule-bottom { top: 745px; }
  .expertise {
    position: absolute; left: 0; top: 530px; width: 100%;
    text-align: center; color: var(--ink-light);
    font-weight: 500; font-size: 54px; line-height: 56px;
  }
  .phone {
    position: absolute; left: 0; top: 790px; width: 100%;
    color: var(--ink-dark); font-weight: 700; text-align: center;
  }
  .phone-area {
    display: flex; align-items: center; justify-content: center; gap: 22px;
    font-size: 96px; line-height: 100px;
  }
  .phone-icon { width: 72px; height: 72px; }
  .phone-number {
    font-size: 94px; line-height: 110px; letter-spacing: 0.06em;
  }
  .ad-band {
    position: absolute; left: 0; top: 1018px; width: 100%; height: 160px;
    background: var(--band);
  }
  .ad-band-text {
    position: absolute; left: 95px; right: 94px; top: 48px;
    display: flex; justify-content: space-between;
    font-family: "Oswald", sans-serif; font-weight: 600;
    font-size: 72px; line-height: 72px; color: #ffffff;
  }
  .ad-band-base {
    position: absolute; left: 0; top: 1178px; width: 100%; height: 22px;
    background: var(--band-dark);
  }
</style>
</head>
<body>
  <main class="panel">
    <div class="illustration" role="img" aria-label="Hand-drawn illustration of two cheerful cartoon figures, one in a nurse cap, carrying a large light blue tooth"></div>

    <h1 class="doctor-name">ROSALIND VARDEN<br>D.D.S.</h1>

    <div class="rule rule-top"></div>
    <p class="expertise">General Dentistry<br>&amp;<br>Orthodontics</p>
    <div class="rule rule-bottom"></div>

    <div class="phone">
      <div class="phone-area">
        <svg class="phone-icon" viewBox="0 0 72 72" aria-hidden="true">
          <circle cx="36" cy="36" r="33" fill="none" stroke="#000" stroke-width="3"/>
          <path d="M40 16 c-6 -2 -12 4 -14 12 c-3 11 0 22 8 27 c3 2 7 1 9 -2 l2 -4 l-7 -5 l-3 3 c-4 -4 -5 -12 -2 -18 l4 -1 l2 -9 z" fill="#000"/>
        </svg>
        <span>(415)</span>
      </div>
      <div class="phone-number">555-0187</div>
    </div>

    <div class="ad-band">
      <div class="ad-band-text">
        <span>C</span><span>A</span><span>L</span><span>L</span><span>&nbsp;</span><span>F</span><span>O</span><span>R</span><span>&nbsp;</span><span>A</span>
      </div>
    </div>
    <div class="ad-band-base"></div>
  </main>
</body>
</html>
```